Start up Dialysis Clinic needs its first website - Velmira Health

Create a visually appealing and user-friendly website for Velmira Health, a dialysis clinic located in Mt. Irvine, Tobago. The website should effectively communicate our services to local, regional, and international patients, providing essential information and fostering trust and engagement..
Key Goals:

1. Informative: Provide comprehensive information about our services, facility, and team.
2. User-Friendly: Ensure the website is easy to navigate, with a clear structure and accessible content.
3. Engaging: Create a visually appealing design that reflects the professionalism and care of Velmira Health.
4. Responsive: Ensure the website is fully responsive and performs well on all devices, including desktops, tablets, and smartphones.
5. Trust-Building: Include testimonials, credentials, and patient resources to build trust with potential patients.
Scope of Work:

1. Home Page: An inviting and informative landing page that provides an overview of our clinic, mission, and services. Include a call to action for more information and contact details.
2. About Us: A detailed page about Velmira Health, including our mission, vision, team, and facility tour.
3. Services: A comprehensive page describing the dialysis services we offer, including Hemodialysis, Peritoneal Dialysis, and Home Hemodialysis.
4. Patient Information: A resourceful section with guides for new patients, FAQs, insurance and billing information, and downloadable forms.
5. Resources: Educational content about kidney health, dialysis options, diet and nutrition tips, and support groups.
6. Contact Us: A contact page with our address, phone number, email, office hours, a contact form, and a map.

```html
<!DOCTYPE html>
<html lang="en">
<head>
<meta charset="utf-8">
<title>Velmira Health — Dialysis Clinic</title>
<link rel="stylesheet" href="https://fonts.googleapis.com/css2?family=Open+Sans:wght@400;500;600;700;800&display=swap">
<style>
:root{
  --navy:#0d1c3d;
  --navy-deep:#0a1530;
  --blue:#3d6fb6;
  --green:#4a8c2a;
  --green-bright:#5a9c2e;
  --orange:#f39a2b;
  --ink:#1a1a1a;
  --muted:#8a8f98;
  --steps-bg:#e9edf4;
  --card-bg:#f7f6f1;
  --white:#ffffff;
}
*{margin:0;padding:0;box-sizing:border-box}
html,body{width:1200px;height:4189px;overflow:hidden}
body{position:relative;font-family:"Open Sans",sans-serif;color:var(--ink);background:var(--white)}
.abs{position:absolute}
svg{display:block}

/* top bar */
.topbar{left:385px;top:0;width:815px;height:32px;background:var(--navy);display:flex;align-items:center;font-size:11px;color:#fff;font-weight:600}
.topbar .item{display:flex;align-items:center;gap:8px;padding:0 22px;height:100%}
.topbar .appt{background:var(--green);padding:0 24px;font-size:10px;letter-spacing:.3px}
.brand{left:88px;top:14px;display:flex;align-items:center;gap:8px}
.brand .mark{width:34px;height:34px;background:var(--green)}
.brand .name{font-size:19px;font-weight:700;color:var(--blue);line-height:1.05}
.nav{left:395px;top:60px;display:flex;gap:0;font-size:11px;font-weight:600;color:#333}
.nav a{color:inherit;text-decoration:none;margin-right:40px}
.nav a:nth-child(5){margin-left:22px}
.btn-outline{left:930px;top:53px;width:118px;height:30px;border:1.5px solid var(--orange);border-radius:4px;color:var(--orange);font-size:11px;display:flex;align-items:center;justify-content:center}

/* hero */
.hero-photo{left:0;top:97px;width:1200px;height:680px;background:linear-gradient(90deg,#ffffff 0%,#f6f8fa 28%,#c8d3dc 48%,#9aa9b8 62%,#6f8aa6 78%,#8fb4cf 100%)}
.hero-kicker{left:124px;top:264px;font-size:20px;font-weight:600;letter-spacing:5px;color:var(--ink)}
.hero-title{left:118px;top:305px;font-size:68px;font-weight:800;color:var(--navy);line-height:1.1}
.hero-rule{left:124px;top:402px;width:497px;height:2px;background:var(--green)}
.hero-text{left:124px;top:424px;width:490px;font-size:15px;line-height:28px;color:#222}
.pill{height:40px;border-radius:20px;color:#fff;font-size:14px;font-weight:700;display:flex;align-items:center;justify-content:center}
.pill.green{left:124px;top:511px;width:146px;background:var(--green)}
.pill.black{left:281px;top:511px;width:180px;background:#000}
.hero-wave{left:0;top:690px}

/* section headings */
.kicker{width:1200px;text-align:center;font-size:13px;font-weight:500;color:var(--green)}
.kicker span{display:inline-block;border-bottom:2px solid var(--green);padding-bottom:4px}
.heading{width:1200px;text-align:center;font-size:40px;font-weight:600;color:var(--navy)}
.heading em{font-style:normal;color:var(--blue)}

/* who we are */
.about-photo{left:120px;top:972px;width:495px;height:340px;border-radius:10px;background:linear-gradient(135deg,#d9e3ea,#a9b8c5 45%,#6c7c8a 80%,#3d4b58)}
.about-card{left:561px;top:998px;width:517px;height:306px;background:var(--card-bg);border-radius:8px;padding:50px 36px 0}
.about-card h3{font-size:20px;font-weight:500;color:var(--ink);margin-bottom:14px}
.about-card p{font-size:12px;line-height:19.5px;color:var(--muted);margin-bottom:10px}
.btn-green{background:var(--green);color:#fff;font-size:14px;font-weight:600;display:flex;align-items:center;justify-content:center;gap:12px;border-radius:2px}
.about-card .btn-green{width:136px;height:39px;margin-top:34px;margin-left:4px}

/* services */
.services-band{left:0;top:1416px;width:1200px;height:555px;background:linear-gradient(90deg,#2b3952 0%,#3a4a63 40%,#2f3f58 70%,#26344b 100%)}
.services-band .kicker{color:#fff}
.services-band .kicker span{border-color:#fff}
.services-band .heading{color:#fff}
.svc{top:1605px;width:304px;height:228px}
.svc.featured{left:119px;background:rgba(86,160,42,.88);color:#fff;text-align:center;padding:76px 34px 0}
.svc.featured h4{font-size:16px;font-weight:700;margin-bottom:6px}
.svc.featured p{font-size:13px;line-height:21px}
.svc.photo{display:flex;align-items:flex-end;padding:0 0 22px 34px;color:#fff;gap:18px}
.svc.photo.p1{left:447px;background:linear-gradient(180deg,#5c6670 0%,#2d3338 50%,#0d0f12 100%)}
.svc.photo.p2{left:776px;background:linear-gradient(180deg,#c9b9c2 0%,#8e6f78 45%,#1a1417 100%)}
.svc.photo h4{font-size:16px;font-weight:700;margin-bottom:6px}
.svc.photo p{font-size:13px}
.services-band .btn-green{left:548px;top:1883px;width:136px;height:39px;position:absolute}

/* steps */
.steps-band{left:0;top:1971px;width:1200px;height:499px;background:var(--steps-bg)}
.step-line{left:338px;top:2236px;width:516px;height:2px;background:var(--blue)}
.step{top:2180px;width:280px;text-align:center}
.step .ring{width:116px;height:116px;margin:0 auto;border-radius:50%;border:2px solid var(--blue);padding:7px;background:var(--steps-bg);position:relative}
.step .core{width:100%;height:100%;border-radius:50%;background:var(--navy);display:flex;align-items:center;justify-content:center}
.step .num{position:absolute;right:-14px;top:44px;width:26px;height:26px;border-radius:50%;background:var(--green);border:2px solid #fff;color:#fff;font-size:10px;font-weight:700;display:flex;align-items:center;justify-content:center}
.step h4{font-size:18px;font-weight:600;color:var(--navy);margin-top:24px}
.step p{font-size:13px;line-height:21px;color:var(--muted);margin:6px auto 0;width:200px}

/* embrace */
.embrace-band{left:0;top:2470px;width:1200px;height:576px;background:linear-gradient(90deg,#3a4660,#2b3650 60%,#28324b)}
.embrace-photo{left:0;top:2470px}
.embrace-kicker{left:635px;top:2563px;font-size:12px;color:var(--green-bright);border-bottom:1px solid var(--green-bright);padding-bottom:2px}
.embrace-title{left:635px;top:2598px;font-size:38px;font-weight:600;line-height:48px;color:#fff}
.feature{left:630px;display:flex;align-items:center;gap:14px;color:#fff}
.feature .ic{width:62px;height:62px;border-radius:50%;background:#fff;display:flex;align-items:center;justify-content:center}
.feature h5{font-size:19px;font-weight:600}
.feature p{font-size:13px;opacity:.85;margin-top:2px}

/* testimonials */
.t-kicker{top:3190px;width:1200px;text-align:center;font-size:17px;color:var(--green)}
.t-heading{top:3220px;font-size:32px}
.quote-badge{left:567px;top:3303px;width:60px;height:60px;border-radius:50%;background:var(--green);display:flex;align-items:center;justify-content:center}
.t-text{left:295px;top:3378px;width:610px;text-align:center;font-size:15px;line-height:23px;color:#222}
.t-name{top:3482px;width:1200px;text-align:center;font-size:13px;color:var(--orange)}
.t-role{top:3503px;width:1200px;text-align:center;font-size:10px;color:#222}
.arrow-btn{top:3543px;width:42px;height:42px;border-radius:50%;display:flex;align-items:center;justify-content:center}
.arrow-btn.prev{left:548px;background:var(--navy)}
.arrow-btn.next{left:602px;background:var(--green)}
.avatar{border-radius:50%;border:3px solid #fff;box-shadow:0 2px 8px rgba(0,0,0,.25)}

/* footer */
.footer-wave{left:0;top:3690px}
.footer{left:0;top:3760px;width:1200px;height:370px;background:var(--navy-deep)}
.f-brand{top:3810px;width:1200px;display:flex;flex-direction:column;align-items:center;gap:10px}
.f-brand .mark{width:64px;height:64px;border:3px solid #fff}
.f-brand .name{font-size:30px;font-weight:600;color:#fff;letter-spacing:.5px}
.f-nav{top:3948px;left:296px;display:flex;font-size:15px;color:#fff}
.f-nav span{margin-right:48px}
.f-rule{left:141px;top:4002px;width:918px;height:1px;background:#3a4560}
.f-contact{top:4048px;display:flex;align-items:center;gap:14px;color:#fff}
.f-contact .ic{width:56px;height:56px;border-radius:50%;border:1.5px solid #fff;display:flex;align-items:center;justify-content:center}
.f-contact .t{font-size:12px;line-height:18px}
.f-contact .t b{font-weight:500;font-size:14px}
.f-sep{top:4036px;width:1px;height:60px;background:#56607a}
.bottom-bar{left:0;top:4130px;width:1200px;height:59px;background:var(--green);color:#fff;font-size:12px}
.bottom-bar .copy{position:absolute;left:147px;top:21px}
.socials{position:absolute;left:932px;top:16px;display:flex;gap:8px}
.socials span{width:25px;height:25px;border:1.5px solid #fff;border-radius:3px;display:block}
</style>
</head>
<body>

<!-- Header -->
<div class="abs brand"><div class="mark"></div><div class="name">Velmira Health</div></div>
<div class="abs topbar">
  <div class="item">
    <svg width="14" height="14" viewBox="0 0 24 24" fill="none" stroke="#fff" stroke-width="2"><path d="M22 16.9v3a2 2 0 0 1-2.2 2 19.8 19.8 0 0 1-8.6-3.1 19.5 19.5 0 0 1-6-6A19.8 19.8 0 0 1 2.1 4.2 2 2 0 0 1 4.1 2h3a2 2 0 0 1 2 1.7c.1.9.4 1.8.7 2.7a2 2 0 0 1-.5 2.1L8 9.8a16 16 0 0 0 6 6l1.3-1.3a2 2 0 0 1 2.1-.4c.9.3 1.8.6 2.7.7a2 2 0 0 1 1.7 2z"/></svg>
    868 - 555 - 0142</div>
  <div class="item appt">
    <svg width="14" height="14" viewBox="0 0 24 24" fill="none" stroke="#fff" stroke-width="2"><rect x="3" y="4" width="18" height="18" rx="2"/><path d="M3 10h18M8 2v4M16 2v4"/></svg>
    REQUEST AN APPOINTMENT</div>
  <div class="item">
    <svg width="12" height="14" viewBox="0 0 24 24" fill="none" stroke="#fff" stroke-width="2"><path d="M12 22s8-7 8-13a8 8 0 0 0-16 0c0 6 8 13 8 13z"/><circle cx="12" cy="9" r="3"/></svg>
    12 Shore Road, Mt. Irvine</div>
</div>
<nav class="abs nav"><a>Home</a><a>About Us</a><a>Solutions</a><a>Projects</a><a>Our Team</a></nav>
<div class="abs btn-outline">CONTACT US</div>

<!-- Hero -->
<div class="abs hero-photo" role="img" aria-label="Two masked clinicians in a bright hospital corridor reviewing a clipboard"></div>
<div class="abs hero-kicker">Experts in</div>
<div class="abs hero-title">Dialysis</div>
<div class="abs hero-rule"></div>
<p class="abs hero-text">Lorem ipsum dolor sit amet, consectetur adipiscing elit, sed do eiusmod tempor incididunt ut labore</p>
<div class="abs pill green">LEARN MORE</div>
<div class="abs pill black">REQUEST QUOTE</div>
<svg class="abs hero-wave" width="1200" height="90" viewBox="0 0 1200 90">
  <defs><linearGradient id="hw" x1="0" x2="1"><stop offset="0" stop-color="#1f3e6e"/><stop offset=".45" stop-color="#3b6a55"/><stop offset="1" stop-color="#4a8c2a"/></linearGradient></defs>
  <path d="M0 40 C250 10 500 50 700 70 C900 85 1080 60 1200 20 L1200 90 L0 90 Z" fill="#fff"/>
  <path d="M0 38 C250 6 500 40 700 58 C900 72 1080 44 1200 8 L1200 30 C1080 62 900 84 700 72 C500 58 250 18 0 42 Z" fill="url(#hw)"/>
</svg>

<!-- Who we are -->
<div class="abs kicker" style="top:844px"><span>WHO WE ARE</span></div>
<h2 class="abs heading" style="top:880px">Recharge your <em>Health</em></h2>
<div class="abs about-photo" role="img" aria-label="Smiling doctor in a white coat with his clinical team"></div>
<div class="abs about-card">
  <h3>Transform your body, transform your life.</h3>
  <p>Lorem ipsum dolor sit amet, consectetur adipiscing elit, sed do eiusmod temp or incididunt ut labore et dolore magna aliqua. Ut enim ad minim veniam, quis laboris nisi ut aliquip ex ea commodo consequat.</p>
  <p>Lorem ipsum dolor sit amet, consectetur adipiscing elit, sed do eiusmod temp or incididunt ut labore et dolore magna aliqua.</p>
  <div class="btn-green">Contact us
    <svg width="16" height="12" viewBox="0 0 16 12" fill="none" stroke="#fff" stroke-width="1.5"><path d="M0 6h14M9 1l5 5-5 5"/></svg></div>
</div>

<!-- Services -->
<div class="abs services-band" role="img" aria-label="Clinician speaking with a patient, dimmed behind a navy overlay">
  <div class="abs kicker" style="top:60px;left:0"><span>OUR SERVICES</span></div>
  <h2 class="abs heading" style="top:94px;left:0">Services We Provide</h2>
</div>
<div class="abs svc featured">
  <h4>Hemodialysis</h4>
  <p>Lorem ipsum dolor sit amet, con sectetur adipiscing elit, sed do eiusmod tempor</p>
  <svg style="margin:12px auto 0" width="28" height="14" viewBox="0 0 28 14" fill="none" stroke="#fff" stroke-width="1.5"><path d="M0 7h26M20 1l6 6-6 6"/></svg>
</div>
<div class="abs svc photo p1" role="img" aria-label="Doctor examining a kidney model through a magnifying glass">
  <svg width="32" height="32" viewBox="0 0 24 24" fill="none" stroke="#5a9c2e" stroke-width="1.5"><path d="M6 18h12M3 22h18M14 22a7 7 0 1 0 0-14M9 14h2M9 12a2 2 0 0 1-2-2V6h6v4a2 2 0 0 1-2 2zM12 6V3a1 1 0 0 0-1-1H9a1 1 0 0 0-1 1v3"/></svg>
  <div><h4>Peritoneal Dialysis</h4><p>Inventore veritasis uas vite</p></div>
</div>
<div class="abs svc photo p2" role="img" aria-label="Patient arm connected to dialysis tubing">
  <svg width="32" height="32" viewBox="0 0 24 24" fill="none" stroke="#5a9c2e" stroke-width="1.5"><path d="M12 2l3 6 7 1-5 5 1 7-6-3-6 3 1-7-5-5 7-1z"/></svg>
  <div><h4>Home Hemodialysis</h4><p>Inventore veritasis uas vite</p></div>
</div>
<div class="btn-green" style="position:absolute;left:548px;top:1883px;width:136px;height:39px">Contact us
  <svg width="16" height="12" viewBox="0 0 16 12" fill="none" stroke="#fff" stroke-width="1.5"><path d="M0 6h14M9 1l5 5-5 5"/></svg></div>

<!-- Steps -->
<div class="abs steps-band"></div>
<div class="abs kicker" style="top:2044px"><span>STEPS TO TAKE</span></div>
<h2 class="abs heading" style="top:2078px"><em>Steps</em> To Take</h2>
<div class="abs step-line"></div>
<div class="abs step" style="left:141px">
  <div class="ring"><div class="core"><svg width="40" height="40" viewBox="0 0 24 24" fill="none" stroke="#fff" stroke-width="1.3"><path d="M6 18h12M3 22h18M14 22a7 7 0 1 0 0-14M9 14h2M9 12a2 2 0 0 1-2-2V6h6v4a2 2 0 0 1-2 2zM12 6V3a1 1 0 0 0-1-1H9a1 1 0 0 0-1 1v3"/></svg></div><div class="num">01</div></div>
  <h4>Contact Us to Start</h4><p>Lorem ipsum dolor sit amet, consectetur adipiscing elit, sed do eiusmo</p>
</div>
<div class="abs step" style="left:457px">
  <div class="ring"><div class="core"><svg width="40" height="40" viewBox="0 0 24 24" fill="none" stroke="#fff" stroke-width="1.3"><path d="M6 18h12M3 22h18M14 22a7 7 0 1 0 0-14M9 14h2M9 12a2 2 0 0 1-2-2V6h6v4a2 2 0 0 1-2 2zM12 6V3a1 1 0 0 0-1-1H9a1 1 0 0 0-1 1v3"/></svg></div><div class="num">02</div></div>
  <h4>Get assigned an expert</h4><p>Lorem ipsum dolor sit amet, consectetur adipiscing elit, sed do eiusmo</p>
</div>
<div class="abs step" style="left:771px">
  <div class="ring"><div class="core"><svg width="40" height="40" viewBox="0 0 24 24" fill="none" stroke="#fff" stroke-width="1.3"><path d="M6 18h12M3 22h18M14 22a7 7 0 1 0 0-14M9 14h2M9 12a2 2 0 0 1-2-2V6h6v4a2 2 0 0 1-2 2zM12 6V3a1 1 0 0 0-1-1H9a1 1 0 0 0-1 1v3"/></svg></div><div class="num">03</div></div>
  <h4>Start the Sessions</h4><p>Lorem ipsum dolor sit amet, consectetur adipiscing elit, sed do eiusmo</p>
</div>

<!-- Embrace -->
<div class="abs embrace-band"></div>
<svg class="abs embrace-photo" width="1200" height="576" viewBox="0 0 1200 576" role="img" aria-label="Female doctor in a white coat holding a tablet beside a patient">
  <defs><linearGradient id="ep" x1="0" x2="1"><stop offset="0" stop-color="#3a3a38"/><stop offset=".35" stop-color="#cfd5dc"/><stop offset=".7" stop-color="#8c96a4"/><stop offset="1" stop-color="#4c5667"/></linearGradient></defs>
  <path d="M0 0 H382 L667 576 H0 Z" fill="url(#ep)"/>
</svg>
<div class="abs embrace-kicker">WHO WE ARE</div>
<h2 class="abs embrace-title">Embrace the journey,<br>see the results.</h2>
<div class="abs feature" style="top:2707px">
  <div class="ic"><svg width="28" height="28" viewBox="0 0 24 24" fill="none" stroke="#4a8c2a" stroke-width="1.5"><path d="M6 18h12M3 22h18M14 22a7 7 0 1 0 0-14M9 14h2M9 12a2 2 0 0 1-2-2V6h6v4a2 2 0 0 1-2 2zM12 6V3a1 1 0 0 0-1-1H9a1 1 0 0 0-1 1v3"/></svg></div>
  <div><h5>On-Time Appointments</h5><p>Inventore veritasis uasvitae dicta suntetur sipid</p></div>
</div>
<div class="abs feature" style="top:2787px">
  <div class="ic"><svg width="28" height="28" viewBox="0 0 24 24" fill="none" stroke="#1a3a6a" stroke-width="1.5"><path d="M3 18v-6a9 9 0 0 1 18 0v6"/><rect x="3" y="15" width="4" height="6" rx="1"/><rect x="17" y="15" width="4" height="6" rx="1"/></svg></div>
  <div><h5>Experienced Professionals</h5><p>Inventore veritasis uasvitae dicta suntetur sipid</p></div>
</div>
<div class="abs feature" style="top:2870px">
  <div class="ic"><svg width="28" height="28" viewBox="0 0 24 24" fill="none" stroke="#4a8c2a" stroke-width="1.5"><path d="M12 2l3 6 7 1-5 5 1 7-6-3-6 3 1-7-5-5 7-1z"/></svg></div>
  <div><h5>Confidentiality</h5><p>Inventore veritasis uasvitae dicta suntetur sipid</p></div>
</div>

<!-- Testimonials -->
<div class="abs t-kicker">TESTIMONIALS</div>
<h2 class="abs heading t-heading">What Our <em>Clients</em> are Saying</h2>
<div class="abs avatar" style="left:90px;top:3360px;width:102px;height:102px;background:linear-gradient(135deg,#4a4f58,#1f242b)" role="img" aria-label="Client portrait"></div>
<div class="abs avatar" style="left:242px;top:3302px;width:58px;height:58px;background:linear-gradient(135deg,#e6e3dd,#3a3f48)" role="img" aria-label="Client portrait"></div>
<div class="abs avatar" style="left:263px;top:3413px;width:42px;height:42px;background:linear-gradient(135deg,#e0d8cf,#9a8c80)" role="img" aria-label="Client portrait"></div>
<div class="abs avatar" style="left:173px;top:3497px;width:84px;height:84px;background:linear-gradient(135deg,#6e5346,#2a2320)" role="img" aria-label="Client portrait"></div>
<div class="abs avatar" style="left:893px;top:3307px;width:50px;height:50px;background:linear-gradient(135deg,#c6c2bd,#5d5550)" role="img" aria-label="Client portrait"></div>
<div class="abs avatar" style="left:896px;top:3430px;width:56px;height:56px;background:linear-gradient(135deg,#d9d3cc,#6a5b52)" role="img" aria-label="Client portrait"></div>
<div class="abs avatar" style="left:1003px;top:3351px;width:106px;height:106px;background:linear-gradient(135deg,#dfe3e8,#7c6d62)" role="img" aria-label="Client portrait"></div>
<div class="abs avatar" style="left:996px;top:3498px;width:80px;height:80px;background:linear-gradient(135deg,#eceae6,#8a8883)" role="img" aria-label="Client portrait"></div>
<div class="abs quote-badge"><svg width="26" height="22" viewBox="0 0 26 22" fill="#fff"><path d="M0 10h8v12H0zM0 10C0 4 3 1 9 0v3C5 4 4 6 4 10zM14 10h8v12h-8zM14 10c0-6 3-9 9-10v3c-4 1-5 3-5 7z"/></svg></div>
<p class="abs t-text">Lorem ipsum dolor sit amet, consectetur adipiscing elit, sed do eiusmod tempor incidi dunt ut labore et dolore magna aliqua .dipiscing elit, sed do eiusmod tempor incidi dunt ut labore et dolore magna aliqua .dipiscing elit, sed do eiusmod tempor incididunt</p>
<div class="abs t-name">Marlon Reyes</div>
<div class="abs t-role">Client</div>
<div class="abs arrow-btn prev"><svg width="18" height="14" viewBox="0 0 18 14" fill="none" stroke="#fff" stroke-width="1.6"><path d="M18 7H2M7 1L1 7l6 6"/></svg></div>
<div class="abs arrow-btn next"><svg width="18" height="14" viewBox="0 0 18 14" fill="none" stroke="#fff" stroke-width="1.6"><path d="M0 7h16M11 1l6 6-6 6"/></svg></div>

<!-- Footer -->
<svg class="abs footer-wave" width="1200" height="80" viewBox="0 0 1200 80">
  <defs><linearGradient id="fw" x1="0" x2="1"><stop offset="0" stop-color="#3d6fb6"/><stop offset=".5" stop-color="#2d5a7a"/><stop offset="1" stop-color="#4a8c2a"/></linearGradient></defs>
  <path d="M0 60 C250 0 450 10 650 30 C850 50 1050 45 1200 10 L1200 80 L0 80 Z" fill="url(#fw)"/>
  <path d="M0 72 C250 20 450 24 650 40 C850 58 1050 56 1200 24 L1200 80 L0 80 Z" fill="#0a1530"/>
</svg>
<div class="abs footer"></div>
<div class="abs f-brand"><div class="mark"></div><div class="name">Velmira Health</div></div>
<div class="abs f-nav"><span>HOME</span><span>SERVICES</span><span>ABOUT US</span><span>TESTIMONIALS</span><span>BLOG</span></div>
<div class="abs f-rule"></div>
<div class="abs f-contact" style="left:142px">
  <div class="ic"><svg width="28" height="28" viewBox="0 0 24 24" fill="none" stroke="#fff" stroke-width="1.3"><circle cx="12" cy="12" r="10"/><path d="M2 12h20M12 2a15 15 0 0 1 0 20M12 2a15 15 0 0 0 0 20"/></svg></div>
  <div class="t">12 Shore Road, Mt. Irvine,<br>Tobago, West Indies</div>
</div>
<div class="abs f-sep" style="left:398px"></div>
<div class="abs f-contact" style="left:474px">
  <div class="ic"><svg width="24" height="28" viewBox="0 0 24 24" fill="none" stroke="#fff" stroke-width="1.3"><rect x="6" y="2" width="12" height="20" rx="2"/><path d="M11 18h2"/></svg></div>
  <div class="t"><b>PHONE</b><br>(868) 555 0142</div>
</div>
<div class="abs f-sep" style="left:718px"></div>
<div class="abs f-contact" style="left:795px">
  <div class="ic"><svg width="28" height="28" viewBox="0 0 24 24" fill="none" stroke="#fff" stroke-width="1.3"><rect x="3" y="6" width="18" height="14" rx="1"/><path d="M3 7l9 7 9-7"/></svg></div>
  <div class="t"><b>EMAIL</b><br>care@velmirahealth.com</div>
</div>
<div class="abs bottom-bar">
  <div class="copy">Velmira Health</div>
  <div class="socials"><span></span><span></span><span></span><span></span></div>
</div>

</body>
</html>
```